Zenqo - revolutionary mobile payment

The app is a P2P money trasfert, without the using of credit card or bank circuits it can transfer electronic money from one person to another consumers simply and immediatelly.
You can use the color you want, but the message we need to transert to consumer is simplicity, safety and coolness.
In attach the logo of the company and the wireframe of thre page of the app.
The goal is to design the page of the app with a clear, simple and intuitive graphic.
Updates

I have upgrade the brief with important information and detail, many thanks

Target Market(s)

all the people

Industry/Entity Type

Credit Card

Requirements
Must have
• You have to design one icon for each button in the first page, (shop is: where to shop)
in the second one a new intuitive image (instead of the hand) that let the user to understand that with a simple swipe he can process the payment
Nice to have
• You can include or esxclude what you want or belive can improve user experience of the app
Should not have
• too much color, too much button or information

```html
<!DOCTYPE html>
<html lang="it">
<head>
<meta charset="utf-8">
<title>Zenqo – Movimenti</title>
<link rel="stylesheet" href="https://fonts.googleapis.com/css2?family=Poppins:wght@300;400;600&display=swap">
<style>
  :root{
    --stage:#c6c9ce;
    --status:#0b0b0d;
    --bar:#f4f5f7;
    --brand:#1f3d86;
    --header:#3c5088;
    --header-deep:#24396f;
    --row:#1f3468;
    --row-edge:#2b4584;
    --text-light:#ffffff;
    --red:#b01f27;
    --green:#28a045;
    --body-top:#a9adc4;
    --body-mid:#4f6fa0;
    --body-low:#c9c7d6;
  }
  *{box-sizing:border-box;margin:0;padding:0}
  html,body{width:1200px;height:1195px;overflow:hidden;background:var(--stage)}
  body{font-family:"Poppins",sans-serif;color:var(--text-light)}
  .screen{position:absolute;left:320px;top:100px;width:560px;height:994px;overflow:hidden;
    background:radial-gradient(ellipse 70% 45% at 55% 55%,var(--body-mid),transparent 75%),
               linear-gradient(180deg,var(--body-top),#8f95b4 45%,var(--body-low));
    box-shadow:0 20px 50px rgba(0,0,0,.25)}
  .status-bar{height:35px;background:var(--status);display:flex;align-items:center;justify-content:space-between;padding:0 14px;font-size:16px}
  .status-bar .carrier{display:flex;align-items:center;gap:6px}
  .status-bar .battery{display:flex;align-items:center;gap:6px}
  .top-bar{height:70px;background:var(--bar);display:flex;align-items:center;justify-content:space-between;padding:0 20px}
  .brand{display:flex;align-items:center;gap:8px;color:var(--brand);font-weight:600;font-size:30px;letter-spacing:.5px}
  .brand-dot{width:30px;height:30px;border-radius:50%;background:var(--brand)}
  .header{position:relative;height:180px;background:linear-gradient(180deg,#4a5d93,var(--header))}
  .back{position:absolute;left:0;top:0;width:110px;height:100%;background:var(--header-deep);display:flex;align-items:center;justify-content:center;font-size:20px;font-weight:300}
  .balance{position:absolute;left:150px;top:50px}
  .balance-label{font-size:20px;font-weight:400}
  .balance-value{font-size:44px;font-weight:600;line-height:1.1}
  .avatar{position:absolute;right:40px;top:10px;width:120px;height:120px;border-radius:50%;border:5px solid #fff;
    background:radial-gradient(circle at 50% 40%,#a3906f,#4e6a3a 70%,#2f4a2a)}
  .period{position:absolute;right:18px;top:140px;background:var(--header-deep);padding:6px 14px;font-size:15px;display:flex;align-items:center;gap:14px}
  .ledger{list-style:none;position:absolute;left:80px;right:20px;top:305px}
  .entry{height:52px;margin-bottom:10px;display:flex;align-items:center;background:var(--row);border-top:1px solid var(--row-edge);box-shadow:0 4px 10px rgba(10,20,50,.25)}
  .entry-icon{width:56px;display:flex;justify-content:center}
  .entry-number{flex:1;font-size:20px;font-weight:300;letter-spacing:.5px}
  .entry-amount{width:90px;font-size:19px;font-weight:600}
  .entry-go{width:44px;height:100%;display:flex;align-items:center;justify-content:center;border-left:1px solid var(--row-edge)}
  .actions{position:absolute;left:80px;right:20px;top:790px;display:flex;justify-content:space-between}
  .action{width:220px;height:82px;display:flex;align-items:center;justify-content:center;font-size:24px;font-weight:600;box-shadow:0 6px 14px rgba(0,0,0,.3)}
  .action-report{background:var(--red)}
  .action-pockets{background:var(--green)}
</style>
</head>
<body>
<main class="screen">
  <div class="status-bar">
    <span class="carrier">●●●○○ NOVA
      <svg width="18" height="14" viewBox="0 0 18 14"><path d="M1 5a12 12 0 0 1 16 0M4 8a7.5 7.5 0 0 1 10 0M7 11a3 3 0 0 1 4 0" stroke="#fff" stroke-width="2" fill="none"/></svg>
    </span>
    <span class="clock">4:21 PM</span>
    <span class="battery">22%
      <svg width="30" height="14" viewBox="0 0 30 14"><rect x="1" y="1" width="25" height="12" rx="2" fill="none" stroke="#fff" stroke-width="1.5"/><rect x="3" y="3" width="6" height="8" fill="#fff"/><rect x="27" y="5" width="2" height="4" fill="#fff"/></svg>
    </span>
  </div>

  <header class="top-bar">
    <svg class="settings" width="34" height="34" viewBox="0 0 24 24" aria-label="Impostazioni"><path fill="#222" d="M19.4 13a7.5 7.5 0 0 0 0-2l2.1-1.6-2-3.5-2.5 1a7 7 0 0 0-1.7-1L15 3h-4l-.4 2.9a7 7 0 0 0-1.7 1l-2.5-1-2 3.5L6.6 11a7.5 7.5 0 0 0 0 2l-2.1 1.6 2 3.5 2.5-1a7 7 0 0 0 1.7 1L11 21h4l.4-2.9a7 7 0 0 0 1.7-1l2.5 1 2-3.5zM13 15.5a3.5 3.5 0 1 1 0-7 3.5 3.5 0 0 1 0 7z"/></svg>
    <div class="brand"><span class="brand-dot"></span>Zenqo</div>
  </header>

  <section class="header">
    <div class="back">‹ Indietro</div>
    <div class="balance">
      <p class="balance-label">Il Tuo Saldo</p>
      <p class="balance-value">€106.82</p>
    </div>
    <div class="avatar" role="img" aria-label="Foto profilo dell'utente"></div>
    <div class="period">Ultimi 30 Giorni
      <svg width="12" height="8" viewBox="0 0 12 8"><path d="M1 1l5 5 5-5" stroke="#fff" stroke-width="2" fill="none"/></svg>
    </div>
  </section>

  <ul class="ledger">
    <li class="entry"><span class="entry-icon"><svg width="26" height="22" viewBox="0 0 26 22"><path d="M13 1L1 11h4v10h6v-6h4v6h6V11h4z" fill="#fff"/></svg></span><span class="entry-number">+39 340 555 0142</span><span class="entry-amount">€ 1</span><span class="entry-go"><svg width="14" height="16" viewBox="0 0 14 16"><path d="M1 1l12 7-12 7z" fill="#fff"/></svg></span></li>
    <li class="entry"><span class="entry-icon"><svg width="26" height="22" viewBox="0 0 26 22"><path d="M13 1L1 11h4v10h6v-6h4v6h6V11h4z" fill="#fff"/></svg></span><span class="entry-number">+39 340 555 0142</span><span class="entry-amount">€ -1</span><span class="entry-go"><svg width="14" height="16" viewBox="0 0 14 16"><path d="M1 1l12 7-12 7z" fill="#fff"/></svg></span></li>
    <li class="entry"><span class="entry-icon"><svg width="26" height="22" viewBox="0 0 26 22"><path d="M13 1L1 11h4v10h6v-6h4v6h6V11h4z" fill="#fff"/></svg></span><span class="entry-number">+39 020 555 0187</span><span class="entry-amount">€ 200</span><span class="entry-go"><svg width="14" height="16" viewBox="0 0 14 16"><path d="M1 1l12 7-12 7z" fill="#fff"/></svg></span></li>
    <li class="entry"><span class="entry-icon"><svg width="26" height="22" viewBox="0 0 26 22"><path d="M13 1L1 11h4v10h6v-6h4v6h6V11h4z" fill="#fff"/></svg></span><span class="entry-number">+39 055 555 0163</span><span class="entry-amount">€ 12</span><span class="entry-go"><svg width="14" height="16" viewBox="0 0 14 16"><path d="M1 1l12 7-12 7z" fill="#fff"/></svg></span></li>
    <li class="entry"><span class="entry-icon"><svg width="26" height="22" viewBox="0 0 26 22"><path d="M13 1L1 11h4v10h6v-6h4v6h6V11h4z" fill="#fff"/></svg></span><span class="entry-number">+39 340 555 0142</span><span class="entry-amount">€ -1</span><span class="entry-go"><svg width="14" height="16" viewBox="0 0 14 16"><path d="M1 1l12 7-12 7z" fill="#fff"/></svg></span></li>
    <li class="entry"><span class="entry-icon"><svg width="26" height="22" viewBox="0 0 26 22"><path d="M13 1L1 11h4v10h6v-6h4v6h6V11h4z" fill="#fff"/></svg></span><span class="entry-number">+39 020 555 0187</span><span class="entry-amount">€ 200</span><span class="entry-go"><svg width="14" height="16" viewBox="0 0 14 16"><path d="M1 1l12 7-12 7z" fill="#fff"/></svg></span></li>
    <li class="entry"><span class="entry-icon"><svg width="26" height="22" viewBox="0 0 26 22"><path d="M13 1L1 11h4v10h6v-6h4v6h6V11h4z" fill="#fff"/></svg></span><span class="entry-number">+39 055 555 0163</span><span class="entry-amount">€ 12</span><span class="entry-go"><svg width="14" height="16" viewBox="0 0 14 16"><path d="M1 1l12 7-12 7z" fill="#fff"/></svg></span></li>
  </ul>

  <nav class="actions">
    <a class="action action-report">Report</a>
    <a class="action action-pockets">Tasche</a>
  </nav>
</main>
</body>
</html>
```